Bicycle Tour Schedule on a Business Card

Need to develop a 2 side business card that highlights a series of bike tours on 1 side and a series of events on the other side.
This will be inserted into a card wallet that attaches to a cell phone and will be handed out at an expo. The card wallets are black and red so color must coordinate with both. There is a photo of the card wallets attached.

1 side needs to be devoted to Pedal Vista Trek and the others to KQR Venture events on the other. Dates and websites are very important.

Target Market(s)

Cyclists
Predominantly men ages 40+
Educated, Professionals

Industry/Entity Type

Business

Font styles to use
Serif

Requirements
Must have
• Pedal vista treks logo on 1 side and KQR Venture logo on the other side
• dates and websites clearly visible
• Design of both sides must go together.
• Must be portrait not landscape

```html
<!DOCTYPE html>
<html lang="en">
<head>
<meta charset="utf-8">
<title>Pedal Vista Treks &amp; KQR Venture – Event Cards</title>
<link rel="stylesheet" href="https://fonts.googleapis.com/css2?family=Open+Sans:ital,wght@0,400;0,700;0,800;1,700&display=swap">
<style>
  :root {
    --page-bg: #ece8e1;
    --card-white: #ffffff;
    --tour-blue: #1f5fae;
    --tour-blue-text: #1d62b0;
    --tour-green: #3aa64a;
    --venture-red: #d3142e;
    --venture-blue: #2f6db5;
    --body-gray: #6b6b6b;
    --body-dark: #555555;
  }
  * { box-sizing: border-box; margin: 0; padding: 0; }
  html, body {
    width: 1200px; height: 950px; overflow: hidden;
    background: var(--page-bg);
    font-family: "Open Sans", Arial, sans-serif;
  }
  .card-pair {
    position: relative; width: 1200px; height: 950px;
    display: flex; justify-content: center; align-items: center; gap: 100px;
  }
  .card {
    width: 400px; height: 700px; background: var(--card-white);
    display: flex; flex-direction: column;
    box-shadow: 0 6px 18px rgba(0,0,0,.18);
    text-align: center;
  }
  .card__brand {
    display: flex; align-items: center; justify-content: center; gap: 14px;
    color: var(--card-white);
  }
  .card__brand-name { font-weight: 800; font-size: 30px; line-height: 1.1; }
  .card__body { flex: 1; padding: 34px 30px 0; }
  .card__headline { font-weight: 700; font-size: 22px; line-height: 1.25; margin-bottom: 20px; }
  .event { margin-bottom: 12px; }
  .event__name { font-size: 19px; color: var(--body-gray); line-height: 1.3; }
  .event__date, .event__site { font-size: 19px; font-weight: 700; color: var(--body-dark); line-height: 1.3; }

  /* Tours side */
  .card--tours .card__brand {
    height: 280px; background: var(--tour-blue);
    border-bottom: 4px solid var(--tour-green);
  }
  .brand-dot { width: 34px; height: 34px; border-radius: 50%; background: var(--tour-green); flex: none; }
  .card--tours .card__headline { font-style: italic; color: var(--tour-blue-text); }

  /* Events side */
  .card--events .card__brand {
    height: 250px; background: var(--venture-red);
    border-bottom: 4px solid var(--venture-blue);
  }
  .brand-square { width: 30px; height: 30px; background: var(--card-white); flex: none; }
  .card--events .card__body { padding-top: 26px; }
  .card--events .card__headline { color: var(--venture-red); margin-bottom: 14px; }
  .card--events .event { margin-bottom: 8px; }
</style>
</head>
<body>
<main class="card-pair">
  <section class="card card--tours">
    <header class="card__brand">
      <span class="brand-dot"></span>
      <span class="card__brand-name">Pedal Vista Treks</span>
    </header>
    <div class="card__body">
      <p class="card__headline">Fully supported bike tours. Discover the hidden gems on two wheels</p>
      <div class="event"><p class="event__name">Heart of Colorado</p><p class="event__date">June 26 - July 2, 2016</p></div>
      <div class="event"><p class="event__name">Colorado Front Range Tour</p><p class="event__date">August 14-20, 2016</p></div>
      <div class="event"><p class="event__name">Cape Cod Tour</p><p class="event__date">October 9 -15, 2016</p></div>
      <div class="event"><p class="event__name">Florida Key Tours</p><p class="event__date">November 6-12, 2016 &amp;<br>December 4-10, 2016</p></div>
    </div>
  </section>

  <section class="card card--events">
    <header class="card__brand">
      <span class="brand-square"></span>
      <span class="card__brand-name">KQR Venture</span>
    </header>
    <div class="card__body">
      <p class="card__headline">Tri Spoke Series:<br>Cycling camps for youth</p>
      <div class="event"><p class="event__name">Mountain Bike Camp</p><p class="event__date">July 8-10, 2016</p></div>
      <div class="event"><p class="event__name">Cyclocross Camp</p><p class="event__date">August 26-28, 2016</p><p class="event__site">Trispokeseries.org</p></div>
      <div class="event"><p class="event__name">Front Peak Century Ride</p><p class="event__date">June 18, 2016</p><p class="event__site">Frontpeakcentury.com</p></div>
      <div class="event"><p class="event__name">Ridgeline Park Loop Challenge</p><p class="event__date">July 30, 2016 - Ridgelineloop.com</p></div>
      <div class="event"><p class="event__name">Zany Wheel Ride</p><p class="event__date">September 11, 2016</p><p class="event__site">zanywheelride.com</p></div>
    </div>
  </section>
</main>
</body>
</html>
```